Website Design for The Elder Nook

Please design and code a new website.
Here are the sites I like best:
http://www.voyaglint.com/alternate/
http://www.wheelgiftbay.org
Please make it similar but look at the competitor site (below) for images and wording. This is NOT a car donation site. It's a senior lead placement site like https://www.kinhavenfinder.com. I just like this sites above as a lead generation sites.
Competitor site:
https://www.kinhavenfinder.com (use ideas / verbiage from this site)
Updates
Competitor site:
Coding
Coded - Design and coding required
Number of Pages Required
1 page
Look and feel
Each slider illustrates characteristics of the customer's brand and the style your logo design should communicate.

```html
<!DOCTYPE html>
<html lang="en">
<head>
<meta charset="utf-8">
<title>The Elder Nook – Senior Living Advice</title>
<link rel="stylesheet" href="https://fonts.googleapis.com/css2?family=Exo+2:wght@400;500&family=Montserrat:ital,wght@0,400;0,500;0,600;1,400&display=swap">
<style>
:root{
  --navy:#102a8c;
  --red:#e63a2f;
  --ink:#222;
  --muted:#555;
  --light:#f1f2f4;
  --line:#cfcfcf;
  --black:#0b0b0b;
}
*{box-sizing:border-box;margin:0;padding:0}
html,body{width:1200px;height:2904px;overflow:hidden}
body{position:relative;font-family:"Montserrat",sans-serif;color:var(--ink);background:#fff}
.abs{position:absolute}
.display{font-family:"Exo 2",sans-serif;font-weight:400}
.hl{color:var(--red)}
.divider{position:absolute;left:50%;width:72px;height:3px;margin-left:-36px;display:flex;gap:4px}
.divider span{flex:1;background:var(--navy)}
.divider span+span{background:var(--red)}
.section-title{position:absolute;left:0;width:1200px;text-align:center;font-size:28px;color:var(--navy);letter-spacing:.5px}

/* header */
.header{top:0;left:0;width:1200px;height:83px;background:#fff}
.brand{left:141px;top:16px}
.brand-name{font-family:"Exo 2",sans-serif;font-size:28px;color:var(--navy)}
.brand-tag{display:flex;align-items:center;gap:10px;font-size:11px;color:var(--red);margin-top:2px}
.brand-tag i{display:block;width:22px;height:1px;background:var(--navy)}
.navbar{top:83px;left:0;width:1200px;height:35px;background:var(--navy)}
.nav-item{top:0;height:35px;line-height:35px;font-size:12px;color:#fff;font-weight:500}
.nav-item.active{background:var(--red);padding:0 18px}
.help{left:748px;top:0;width:282px;height:83px;background:var(--red);color:#fff}
.flag{left:955px;top:21px;width:57px;height:34px;border:1px solid #fff}
.flag span{position:absolute;left:11px;top:10px;width:22px;height:14px;background:#fff}
.advisor-strip{left:748px;top:83px;width:282px;height:35px;background:#fff;text-align:center;line-height:35px;font-size:13px;color:var(--ink)}
/* hero */
.hero{top:118px;left:0;width:1200px;height:353px;background:linear-gradient(120deg,#516a2a 0%,#3a3420 45%,#7f8f3a 75%,#a6b45a 100%)}
.hero-text{left:141px;top:296px;font-size:36px;color:#fff;line-height:44px}
.form-panel{left:748px;top:118px;width:282px;height:353px;background:var(--red)}
.form-panel h3{position:absolute;top:22px;width:100%;text-align:center;font-size:13px;color:#fff;font-weight:500}
.field{position:absolute;height:25px;background:#fff;border-radius:2px;font-size:10px;color:var(--muted);padding:0 10px;line-height:25px}
.field.select::after{content:"";position:absolute;right:10px;top:10px;border:4px solid transparent;border-top:5px solid #222}
.btn-search{position:absolute;left:25px;top:262px;width:232px;height:35px;border-radius:18px;background:var(--navy);color:#fff;text-align:center;line-height:35px;font-size:16px;font-family:"Exo 2",sans-serif}

/* services */
.lead{position:absolute;left:380px;width:440px;text-align:center;font-size:12px;line-height:18px;color:var(--ink)}
.service{position:absolute;top:664px;width:180px;text-align:center}
.service .ring{width:117px;height:117px;margin:0 auto;border-radius:50%;border:3px solid var(--navy);padding:4px;background:#fff}
.service .disc{width:100%;height:100%;border-radius:50%;background:var(--red);display:flex;align-items:center;justify-content:center}
.service p{margin-top:15px;font-size:13px;font-weight:600;line-height:18px}

/* cost */
.cost{top:908px;left:0;width:1200px;height:353px;background:linear-gradient(90deg,#4c4a2c 0%,#8b6a40 40%,#b79a76 60%,#7a7d5e 100%)}
.cost-shade{top:908px;left:0;width:1200px;height:353px;background:rgba(10,10,20,.35)}
.cost-text{left:0;width:1200px;text-align:center;color:#fff}
.btn-contact{left:509px;top:1154px;width:182px;height:35px;border-radius:18px;background:var(--navy);color:#fff;font-family:"Exo 2",sans-serif;font-size:17px;display:flex;align-items:center;justify-content:center;gap:14px}

/* advisor cards */
.card{position:absolute;top:1449px;width:283px;height:107px;border:1px solid #bbb;border-radius:3px;background:#fff}
.card svg{position:absolute;left:14px;top:14px}
.card h4{position:absolute;left:71px;top:12px;width:200px;font-size:14.5px;font-weight:400;line-height:20px;color:var(--ink)}
.card p{position:absolute;left:73px;top:62px;font-size:11.5px;line-height:17px;color:var(--muted)}
.finder{left:353px;top:1599px;width:494px;height:35px}
.finder .input{position:absolute;left:0;top:0;width:250px;height:35px;border:1px solid #999;border-right:none;border-radius:18px 0 0 18px;line-height:33px;padding-left:42px;color:#888;font-size:14px}
.finder .go{position:absolute;left:246px;top:0;width:248px;height:35px;background:var(--navy);border-radius:0 18px 18px 0;color:#fff;text-align:center;line-height:35px;font-family:"Exo 2",sans-serif;font-size:17px}

/* testimonials */
.testimonials{top:1704px;left:0;width:1200px;height:425px;background:var(--light)}
.quote{left:0;width:1200px;text-align:center}
.avatar{position:absolute;top:1946px;width:74px;height:74px;border-radius:10px;background:linear-gradient(160deg,#e4e4e4,#bdbdbd)}
.avatar.active{top:1945px;width:76px;height:76px;border:4px solid var(--red);background:linear-gradient(160deg,#7fb3cf,#c99a6f)}
.dot{position:absolute;top:2051px;width:8px;height:8px;border-radius:50%;background:#ccc}

/* states */
.states{left:140px;top:2285px;width:920px;height:387px;background:#fff;border-radius:6px;box-shadow:0 0 10px rgba(0,0,0,.12)}
.tab{position:absolute;top:14px;font-size:13px;font-weight:500;text-align:center;line-height:17px;color:var(--ink);letter-spacing:.5px}
.tab.active{color:var(--red);background:#fff;top:0;height:56px;padding-top:14px;border-radius:6px 6px 0 0;box-shadow:0 -3px 6px rgba(0,0,0,.08)}
.tabbar{position:absolute;left:0;top:0;width:920px;height:56px;background:#f6f6f6;border-radius:6px 6px 0 0}
.state-col{position:absolute;top:82px;list-style:none;font-size:12px;line-height:17px;color:var(--ink);letter-spacing:.3px}

/* footer */
.footer{top:2743px;left:0;width:1200px;height:127px;background:var(--black);color:#fff}
.foot-nav{position:absolute;top:25px;font-size:12px;font-weight:500}
.foot-rule{position:absolute;left:141px;top:52px;width:670px;height:1px;background:#333}
.contact{position:absolute;top:75px;display:flex;gap:8px;font-size:12px;line-height:16px;letter-spacing:.3px}
.contact .ic{width:27px;height:27px;border:1px solid #fff;border-radius:50%;flex:none;display:flex;align-items:center;justify-content:center}
.contact b{font-weight:600}
.copy{top:2870px;left:0;width:1200px;height:34px;background:var(--red);color:#fff;font-size:12px}
.social{position:absolute;top:5px;width:26px;height:26px;border:1px solid #fff;border-radius:50%}
</style>
</head>
<body>

<!-- header -->
<header class="abs header">
  <div class="abs brand">
    <div class="brand-name">The Elder Nook</div>
    <div class="brand-tag"><i></i>Seniorcare Nonprofit<i></i></div>
  </div>
</header>
<nav class="abs navbar">
  <div class="abs nav-item active" style="left:141px">Assisted Living</div>
  <div class="abs nav-item" style="left:296px">Memory Care</div>
  <div class="abs nav-item" style="left:432px">Nursing Homes</div>
  <div class="abs nav-item" style="left:585px">More Living Options ▾</div>
</nav>
<div class="abs help">
  <svg class="abs" style="left:22px;top:38px" width="20" height="20" viewBox="0 0 24 24"><path fill="#fff" d="M6.6 10.8a15 15 0 0 0 6.6 6.6l2.2-2.2c.3-.3.7-.4 1-.2 1.1.4 2.3.6 3.6.6.6 0 1 .4 1 1V20c0 .6-.4 1-1 1A17 17 0 0 1 3 4c0-.6.4-1 1-1h3.5c.6 0 1 .4 1 1 0 1.2.2 2.4.6 3.6.1.3 0 .7-.2 1z"/></svg>
  <div class="abs" style="left:52px;top:18px;font-size:16px">Need help? Call</div>
  <div class="abs display" style="left:52px;top:36px;font-size:21px">555-204-7781</div>
</div>
<div class="abs flag"><span></span><svg class="abs" style="left:40px;top:14px" width="8" height="6"><path d="M0 0h8L4 5z" fill="#fff"/></svg></div>
<div class="abs advisor-strip">Talk to a local advisor for FREE</div>

<!-- hero -->
<div class="abs hero" role="img" aria-label="Elderly couple seen from behind sitting on a park bench on a sunny lawn"></div>
<h1 class="abs hero-text display">You know your family.<br>We know <span class="hl">SENIOR LIVING.</span></h1>
<form class="abs form-panel">
  <h3>Find Senior Living Near You.</h3>
  <div class="field" style="left:25px;top:58px;width:106px">Firest Name</div>
  <div class="field" style="left:151px;top:58px;width:106px">Last Name</div>
  <div class="field" style="left:25px;top:97px;width:232px">Phone Number</div>
  <div class="field" style="left:25px;top:137px;width:232px">Email Address</div>
  <div class="field select" style="left:25px;top:176px;width:106px">Select State</div>
  <div class="field select" style="left:151px;top:176px;width:106px">select City</div>
  <div class="field" style="left:25px;top:216px;width:232px">Zip Code</div>
  <div class="btn-search">Start Your Search</div>
</form>

<!-- support -->
<h2 class="section-title display" style="top:535px">The support you need to make the <span class="hl">RIGHT CHOICE</span></h2>
<div class="divider" style="top:583px"><span></span><span></span></div>
<p class="lead" style="top:603px">Kin Haven has already helped thousands of families find peace of mind. Here's what's included with our free service:</p>

<div class="service" style="left:111px"><div class="ring"><div class="disc">
  <svg width="50" height="54" viewBox="0 0 50 54"><circle cx="25" cy="14" r="13" fill="#fff"/><path d="M2 54v-8c0-9 8-15 16-15h14c8 0 16 6 16 15v8z" fill="#fff"/></svg>
</div></div><p>Dedicated local<br>advisor</p></div>
<div class="service" style="left:311px"><div class="ring"><div class="disc">
  <svg width="56" height="48" viewBox="0 0 56 48"><path d="M28 2 2 24l4 4 4-3v23h14V34h8v14h14V25l4 3 4-4z" fill="#fff"/></svg>
</div></div><p>Hand-picked list of<br>communities to match<br>your needs</p></div>
<div class="service" style="left:510px"><div class="ring"><div class="disc">
  <div class="display" style="color:#fff;font-size:64px;font-weight:500;line-height:1">$</div>
</div></div><p>Full details and<br>pricing</p></div>
<div class="service" style="left:710px"><div class="ring"><div class="disc">
  <svg width="50" height="50" viewBox="0 0 50 50"><rect x="2" y="7" width="46" height="41" rx="3" fill="#fff"/><rect x="12" y="2" width="4" height="10" fill="#fff"/><rect x="34" y="2" width="4" height="10" fill="#fff"/><g fill="#e63a2f"><rect x="7" y="18" width="7" height="6"/><rect x="17" y="18" width="7" height="6"/><rect x="27" y="18" width="7" height="6"/><rect x="37" y="18" width="6" height="6"/><rect x="7" y="27" width="7" height="6"/><rect x="17" y="27" width="7" height="6"/><rect x="27" y="27" width="7" height="6"/><rect x="37" y="27" width="6" height="6"/><rect x="7" y="36" width="7" height="6"/><rect x="17" y="36" width="7" height="6"/><rect x="27" y="36" width="7" height="6"/><rect x="37" y="36" width="6" height="6"/></g></svg>
</div></div><p>Help scheduling<br>tours</p></div>
<div class="service" style="left:909px"><div class="ring"><div class="disc">
  <svg width="60" height="48" viewBox="0 0 60 48"><rect x="20" y="4" width="38" height="32" rx="2" fill="#fff"/><path d="M2 22 10 12h8v24H2z" fill="#fff"/><circle cx="12" cy="40" r="6" fill="#fff" stroke="#e63a2f" stroke-width="3"/><circle cx="46" cy="40" r="6" fill="#fff" stroke="#e63a2f" stroke-width="3"/></svg>
</div></div><p>Move in support</p></div>

<!-- cost -->
<div class="abs cost" role="img" aria-label="Smiling caregiver talking with an elderly woman seated in a bright care home"></div>
<div class="abs cost-shade"></div>
<h2 class="abs cost-text display" style="top:973px;font-size:27px">There's no <span class="hl">cost</span> to you.</h2>
<div class="divider" style="top:1021px"><span style="background:#fff"></span><span></span></div>
<p class="abs cost-text" style="top:1042px;font-size:13px;line-height:19px;letter-spacing:.4px">We work with over 20,000 senior living communities.<br>Our community partners pay us for placement<br>services.</p>
<div class="abs cost-text display" style="top:1109px;font-size:21px">
  <svg width="18" height="18" viewBox="0 0 24 24" style="vertical-align:-2px;margin-right:6px"><path fill="#fff" d="M6.6 10.8a15 15 0 0 0 6.6 6.6l2.2-2.2c.3-.3.7-.4 1-.2 1.1.4 2.3.6 3.6.6.6 0 1 .4 1 1V20c0 .6-.4 1-1 1A17 17 0 0 1 3 4c0-.6.4-1 1-1h3.5c.6 0 1 .4 1 1 0 1.2.2 2.4.6 3.6.1.3 0 .7-.2 1z"/></svg>Call555-204-7781</div>
<div class="abs btn-contact">Contact Now <svg width="18" height="16" viewBox="0 0 18 16"><path d="M0 7 18 0l-4 16-5-5 5-7-7 6z" fill="#fff"/></svg></div>

<!-- advisor -->
<h2 class="section-title display" style="top:1325px">Your <span class="hl">LOCAL ADVISOR</span> informs. You decide.</h2>
<div class="divider" style="top:1372px"><span></span><span></span></div>
<p class="lead" style="top:1394px;left:300px;width:600px;font-size:11.5px">Over 400 senior advisors across the U.S. and Canada are ready to help your family with:</p>

<div class="card" style="left:141px">
  <svg width="30" height="56" viewBox="0 0 30 56"><circle cx="15" cy="14" r="12" fill="none" stroke="#e63a2f" stroke-width="2"/><circle cx="12" cy="12" r="3" fill="none" stroke="#e63a2f" stroke-width="2"/><path d="M15 26v28" stroke="#e63a2f" stroke-width="2"/></svg>
  <h4>Insider's tips for the area near you</h4><p>Lorem ipsum dolor sit amet,<br>consectetur adipiscing elit.</p>
</div>
<div class="card" style="left:458px">
  <svg width="46" height="42" viewBox="0 0 46 42"><path d="M23 40 5 22A11 11 0 0 1 23 7a11 11 0 0 1 18 15z" fill="none" stroke="#e63a2f" stroke-width="2"/></svg>
  <h4>Advice tailored to your unique situation</h4><p>Lorem ipsum dolor sit amet,<br>consectetur adipiscing elit.</p>
</div>
<div class="card" style="left:775px">
  <svg width="44" height="44" viewBox="0 0 44 44"><circle cx="22" cy="22" r="20" fill="none" stroke="#e63a2f" stroke-width="2"/><path d="M22 8v15H12" fill="none" stroke="#e63a2f" stroke-width="2"/></svg>
  <h4>Time saving know-how and resources</h4><p>Lorem ipsum dolor sit amet,<br>consectetur adipiscing elit.</p>
</div>
<div class="abs finder"><div class="input">Enter city or postal code</div><div class="go">Find An Advisor Near You</div></div>

<!-- testimonials -->
<section class="abs testimonials"></section>
<h2 class="section-title display" style="top:1769px"><span class="hl">97%</span> of our customers recommend our service</h2>
<div class="divider" style="top:1816px"><span></span><span></span></div>
<p class="abs quote" style="top:1847px;font-size:13px;font-style:italic;color:#444">“You were a great help. We really appreciate you &amp; Kin Haven!”</p>
<p class="abs quote" style="top:1882px;font-size:11.5px;font-weight:600;color:#333">DALE M</p>
<p class="abs quote" style="top:1908px;font-size:9.5px;color:#555">Looking for Senior Living for his wife in Denver, CO</p>
<div class="avatar" style="left:454px" role="img" aria-label="Portrait of an older man"></div>
<div class="avatar active" style="left:562px" role="img" aria-label="Portrait of a smiling senior couple at the beach"></div>
<div class="avatar" style="left:672px" role="img" aria-label="Portrait of an older woman"></div>
<div class="dot" style="left:581px;background:#d21e1e"></div>
<div class="dot" style="left:595px"></div>
<div class="dot" style="left:609px"></div>

<!-- states -->
<h2 class="section-title display" style="top:2192px">Senior Living by <span class="hl">State</span></h2>
<div class="divider" style="top:2241px"><span></span><span></span></div>
<div class="abs states">
  <div class="tabbar"></div>
  <div class="tab" style="left:30px">Memory<br>Care</div>
  <div class="tab active" style="left:104px;width:154px">Assisted<br>Living</div>
  <div class="tab" style="left:282px">Independent<br>Living</div>
  <div class="tab" style="left:415px">Nursing<br>Home</div>
  <div class="tab" style="left:554px">Care<br>Homes</div>
  <ul class="state-col" style="left:24px"><li>Alabama</li><li>Arizona</li><li>Arkansas</li><li>California</li><li>Colorado</li><li>Connecticut</li><li>Delaware</li><li>District of Columbia</li><li>Florida</li><li>Georgia</li><li>Hawaii</li><li>Idaho</li><li>Illinois</li><li>Indiana</li><li>Iowa</li><li>Kansas</li><li>Kentucky</li></ul>
  <ul class="state-col" style="left:324px"><li>Louisiana</li><li>Maine</li><li>Maryland</li><li>Massachusetts</li><li>Michigan</li><li>Minnesota</li><li>Mississippi</li><li>Missouri</li><li>Montana</li><li>Nebraska</li><li>Nevada</li><li>New Hampshire</li><li>New Jersey</li><li>New Mexico</li><li>New York</li><li>North Carolina</li><li>North Dakota</li></ul>
  <ul class="state-col" style="left:649px"><li>Ohio</li><li>Oklahoma</li><li>Oregon</li><li>Pennsylvania</li><li>Rhode Island</li><li>South Carolina</li><li>South Dakota</li><li>Tennessee</li><li>Texas</li><li>Utah</li><li>Vermont</li><li>Virginia</li><li>Washington</li><li>West Virginia</li><li>Wisconsin</li><li>Wyoming</li></ul>
</div>

<!-- footer -->
<footer class="abs footer">
  <div class="foot-nav" style="left:141px">Assisted Living</div>
  <div class="foot-nav" style="left:278px">Memory Care</div>
  <div class="foot-nav" style="left:415px">Nursing Homes</div>
  <div class="foot-nav" style="left:567px">More Living Options ▾</div>
  <div class="foot-rule"></div>
  <div class="contact" style="left:182px"><div class="ic"><svg width="10" height="14" viewBox="0 0 10 14"><path d="M5 0a5 5 0 0 1 5 5c0 4-5 9-5 9S0 9 0 5a5 5 0 0 1 5-5z" fill="#2a48c8"/></svg></div><div><b>Address</b><br>48 Sample Lane, Suite 310, Albany,<br>NY 12207</div></div>
  <div class="contact" style="left:470px"><div class="ic"><svg width="12" height="12" viewBox="0 0 24 24"><path fill="#2a48c8" d="M6.6 10.8a15 15 0 0 0 6.6 6.6l2.2-2.2c.3-.3.7-.4 1-.2 1.1.4 2.3.6 3.6.6.6 0 1 .4 1 1V20c0 .6-.4 1-1 1A17 17 0 0 1 3 4c0-.6.4-1 1-1h3.5c.6 0 1 .4 1 1 0 1.2.2 2.4.6 3.6.1.3 0 .7-.2 1z"/></svg></div><div><b>Call Us :</b><br>555-204-7781</div></div>
  <div class="contact" style="left:615px"><div class="ic"><svg width="12" height="9" viewBox="0 0 12 9"><rect width="12" height="9" rx="1" fill="#2a48c8"/></svg></div><div><b>Email Us :</b><br>info@theeldernook.com</div></div>
  <div class="abs" style="left:850px;top:23px;width:210px;text-align:right">
    <div class="display" style="font-size:28px">The Elder Nook</div>
    <div style="display:flex;justify-content:flex-end;align-items:center;gap:10px;font-size:11px;margin-top:2px"><i style="display:block;width:22px;height:1px;background:#fff"></i>Seniorcare Nonprofit<i style="display:block;width:22px;height:1px;background:#fff"></i></div>
  </div>
</footer>
<div class="abs copy">
  <div class="abs" style="left:141px;top:10px">Copyright 2019 The Elder Nook Seniorcare Nonprofit . All Rights Reserved.</div>
  <div class="social" style="left:961px"></div>
  <div class="social" style="left:997px"></div>
  <div class="social" style="left:1033px"></div>
</div>

</body>
</html>
```